New Business Card Design Project LORVANTI-Italy

we are LORVANTI-Italy
our company in the market for 3 years we are luxury cosmetic company and its about time for a facelift :)
i will like to have elegant luxurious and unique business card
that will give the person that get it a unique, luxurious and elegant impression
I'm VERY OPEN FOR NEW IDEAS , even duo i add a few files of things that i see on line and i like them

i add my logo as well
my website is LORVANTI.COM
(if you would like to see the main style that we have)

Target Market(s)

adult that have money :)

Industry/Entity Type

Business

Contact Information for Business Card

Name - Dario Lorvanti
Position - CEO and CO Founder
address - 4817 E Halvern
telephone - 555-384-1926
email - dario@lorvanti.com
fax - 555-384-1926
website - LORVANTI.COM

Colors
000000
959595
fbee3e
ffffff

Requirements
Must have
• big logo in GOLD color
• elegant look
• impressive
Nice to have
• not must but maybe classy pattern background
• not must but maybe emblem
• maybe clear plastic business card
Should not have
• colors
• images

```html
<!DOCTYPE html>
<html lang="en">
<head>
<meta charset="utf-8">
<title>LORVANTI Italy — Business Card</title>
<link href="https://fonts.googleapis.com/css2?family=Open+Sans:wght@400;600&display=swap" rel="stylesheet">
<style>
  :root {
    --backdrop: #2a2725;
    --card-black: #0b0b0b;
    --card-edge: #161616;
    --gold: #d9b550;
    --gold-band: #d8bd5c;
    --text-light: #f2f2f2;
    --text-muted: #b9b9b9;
  }
  * { margin: 0; padding: 0; box-sizing: border-box; }
  html, body { width: 1200px; height: 716px; overflow: hidden; }
  body {
    background: var(--backdrop);
    font-family: "Open Sans", Arial, sans-serif;
    position: relative;
  }
  .card {
    position: absolute;
    width: 540px;
    height: 309px;
    background: linear-gradient(160deg, var(--card-edge), var(--card-black) 60%);
    box-shadow: 0 18px 40px rgba(0,0,0,.55);
    overflow: hidden;
  }
  .card--front { left: 40px; top: 204px; }
  .card--back  { left: 620px; top: 204px; }

  /* Brand mark: plain circle + name */
  .brand { display: flex; flex-direction: column; align-items: center; color: var(--gold); font-weight: 600; }
  .brand__circle { border: 2px solid var(--gold); border-radius: 50%; }
  .brand__name { letter-spacing: .08em; line-height: 1; }
  .brand__country { letter-spacing: .25em; line-height: 1; }

  .card--front .brand { position: absolute; left: 0; right: 0; top: 62px; }
  .card--front .brand__circle { width: 86px; height: 86px; margin-bottom: 18px; }
  .card--front .brand__name { font-size: 44px; }
  .card--front .brand__country { font-size: 14px; margin-top: 10px; }

  .card--back .brand { position: absolute; left: 40px; width: 150px; top: 30px; }
  .card--back .brand__circle { width: 42px; height: 42px; margin-bottom: 8px; }
  .card--back .brand__name { font-size: 22px; }
  .card--back .brand__country { font-size: 8px; margin-top: 5px; }

  .holder { position: absolute; left: 40px; top: 140px; }
  .holder__name { color: var(--text-light); font-size: 15px; font-weight: 600; }
  .holder__role { color: var(--text-muted); font-size: 8px; margin-top: 1px; }

  .contact-line { display: flex; align-items: center; gap: 8px; color: var(--text-light); font-size: 12px; font-weight: 600; line-height: 1.45; }
  .contact-line svg { width: 11px; height: 11px; flex: none; }

  .address { position: absolute; left: 40px; top: 184px; }

  .divider { position: absolute; left: 0; right: 0; top: 214px; height: 1px; background: var(--gold); }

  .contact-group { position: absolute; top: 228px; }
  .contact-group--direct { left: 205px; }
  .contact-group--office { left: 380px; }

  .gold-band { position: absolute; left: 0; right: 0; bottom: 0; height: 22px; background: var(--gold-band); }
</style>
</head>
<body>

  <section class="card card--front" aria-label="Card front">
    <div class="brand">
      <span class="brand__circle"></span>
      <span class="brand__name">LORVANTI</span>
      <span class="brand__country">ITALY</span>
    </div>
  </section>

  <section class="card card--back" aria-label="Card back">
    <div class="brand">
      <span class="brand__circle"></span>
      <span class="brand__name">LORVANTI</span>
      <span class="brand__country">ITALY</span>
    </div>

    <div class="holder">
      <p class="holder__name">Dario Lorvanti</p>
      <p class="holder__role">Position - CEO and CO Founder</p>
    </div>

    <p class="contact-line address">
      <svg viewBox="0 0 12 12" aria-hidden="true"><path d="M6 0.5a4 4 0 0 0-4 4c0 3 4 7 4 7s4-4 4-7a4 4 0 0 0-4-4zm0 5.6a1.6 1.6 0 1 1 0-3.2 1.6 1.6 0 0 1 0 3.2z" fill="var(--gold)"/></svg>
      4817 E Halvern
    </p>

    <div class="divider"></div>

    <div class="contact-group contact-group--direct">
      <p class="contact-line">
        <svg viewBox="0 0 12 12" aria-hidden="true"><path d="M2.5 1h2l1 2.6-1.3 1a6 6 0 0 0 3.2 3.2l1-1.3 2.6 1v2a1 1 0 0 1-1 1A9.5 9.5 0 0 1 1.5 2a1 1 0 0 1 1-1z" fill="var(--gold)"/></svg>
        555-384-1926
      </p>
      <p class="contact-line">
        <svg viewBox="0 0 12 12" aria-hidden="true"><rect x="1" y="2.5" width="10" height="7" fill="none" stroke="var(--gold)" stroke-width="1.1"/><path d="M1 2.5l5 4 5-4" fill="none" stroke="var(--gold)" stroke-width="1.1"/></svg>
        dario@lorvanti.com
      </p>
    </div>

    <div class="contact-group contact-group--office">
      <p class="contact-line">
        <svg viewBox="0 0 12 12" aria-hidden="true"><rect x="3" y="1" width="6" height="3.5" fill="none" stroke="var(--gold)" stroke-width="1"/><rect x="1" y="4.5" width="10" height="5" fill="var(--gold)"/><rect x="3" y="8" width="6" height="3" fill="var(--card-black)" stroke="var(--gold)" stroke-width="1"/></svg>
        555-384-1926
      </p>
      <p class="contact-line">
        <svg viewBox="0 0 12 12" aria-hidden="true"><circle cx="6" cy="6" r="5" fill="none" stroke="var(--gold)" stroke-width="1"/><ellipse cx="6" cy="6" rx="2.2" ry="5" fill="none" stroke="var(--gold)" stroke-width="1"/><path d="M1 6h10" stroke="var(--gold)" stroke-width="1"/></svg>
        LORVANTI.COM
      </p>
    </div>

    <div class="gold-band"></div>
  </section>

</body>
</html>
```